RWT Fittings Ltd Business Cards

We need a business card with our business logo. We provide window and door installations on high-rises in west coast British Colombia, Canada.

I would like my business information and details on one side of the card, and the other side the company name with logo

Target Market(s)

General Contractors

Industry/Entity Type

Construction

Contact Information for Business Card

one side i want my company name and logo in the dark theme logo that i provided

Requirements
Must have
• Marco Peltieri, 16045518293, RWTFittings@mailbox-demo.com, 1407-5194 Linden Row Burnaby BC, V5H 2K9, Owner & Manager

```html
<!DOCTYPE html>
<html lang="en">
<head>
<meta charset="utf-8">
<title>RWT Fittings Ltd — Business Cards</title>
<link rel="stylesheet" href="https://fonts.googleapis.com/css2?family=Montserrat:wght@700;800&family=Poppins:wght@400;500;600&display=swap">
<style>
  :root {
    --backdrop: #d9d9d9;
    --card-white: #ffffff;
    --card-dark: #2b2b2d;
    --card-dark-deep: #1a1a1b;
    --brand-blue: #22a3e0;
    --text-grey: #4a4a4a;
  }
  * { box-sizing: border-box; margin: 0; padding: 0; }
  html, body {
    width: 1200px; height: 900px; overflow: hidden;
    background: var(--backdrop);
    font-family: "Poppins", sans-serif;
  }
  .canvas { position: relative; width: 1200px; height: 900px; }
  .card {
    position: absolute; left: 237px; width: 725px; height: 414px;
    box-shadow: 0 10px 24px rgba(0,0,0,0.22);
    overflow: hidden;
  }
  /* Back side */
  .card-back { top: 20px; background: var(--card-dark); }
  .back-pattern {
    position: absolute; inset: 0;
    background: linear-gradient(160deg, #5a5a5c 0%, var(--card-dark) 45%, var(--card-dark-deep) 100%);
  }
  .back-brand {
    position: absolute; right: 48px; top: 215px;
    display: flex; align-items: center; gap: 12px;
  }
  .brand-square { width: 22px; height: 22px; background: var(--brand-blue); flex: none; }
  .back-brand .brand-name {
    font-weight: 600; font-size: 30px; color: var(--brand-blue); letter-spacing: 0.5px;
  }
  /* Front side */
  .card-front { top: 466px; background: var(--card-white); }
  .front-brand {
    position: absolute; left: 48px; top: 168px;
    display: flex; align-items: center; gap: 16px;
  }
  .front-brand .brand-square { width: 38px; height: 38px; }
  .front-brand .brand-name {
    font-weight: 600; font-size: 36px; color: var(--brand-blue); letter-spacing: 0.5px;
    white-space: nowrap;
  }
  .person { position: absolute; right: 56px; top: 62px; text-align: right; }
  .person-name {
    font-family: "Montserrat", sans-serif; font-weight: 800;
    font-size: 27px; color: var(--brand-blue); letter-spacing: 1.5px;
    text-transform: uppercase; line-height: 1.1;
  }
  .person-title { font-size: 17px; color: var(--text-grey); letter-spacing: 1px; margin-top: 2px; }
  .address {
    position: absolute; right: 84px; top: 250px; text-align: right;
    font-size: 19px; color: var(--text-grey); line-height: 1.3; letter-spacing: 0.5px;
    font-style: normal;
  }
  .contacts { position: absolute; right: 56px; top: 312px; list-style: none; }
  .contact-item {
    display: flex; align-items: center; justify-content: flex-end; gap: 10px;
    font-size: 19px; color: var(--text-grey); line-height: 1.35; letter-spacing: 0.3px;
    white-space: nowrap;
  }
  .contact-icon { width: 18px; height: 18px; flex: none; }
</style>
</head>
<body>
<main class="canvas">
  <section class="card card-back" aria-label="Card back">
    <div class="back-pattern" role="img" aria-label="Repeating dark tonal pattern of the company mark"></div>
    <div class="back-brand">
      <span class="brand-square"></span>
      <span class="brand-name">RWT Fittings Ltd</span>
    </div>
  </section>

  <section class="card card-front" aria-label="Card front">
    <div class="front-brand">
      <span class="brand-square"></span>
      <span class="brand-name">RWT Fittings Ltd</span>
    </div>

    <div class="person">
      <p class="person-name">Marco Peltieri</p>
      <p class="person-title">Owner &amp; Manager</p>
    </div>

    <address class="address">
      1407-5194 Linden Row<br>Burnaby BC, V5H 2K9
    </address>

    <ul class="contacts">
      <li class="contact-item">604-551-8293
        <svg class="contact-icon" viewBox="0 0 24 24" aria-hidden="true"><path d="M6.6 3.5l3 3-2 2.2c1.2 2.6 3.2 4.6 5.8 5.8l2.2-2 3 3-2.4 2.6C10.6 17.6 6.4 13.4 4 7.8z" fill="none" stroke="#22a3e0" stroke-width="2" stroke-linejoin="round"/></svg>
      </li>
      <li class="contact-item">RWTFittings@mailbox-demo.com
        <svg class="contact-icon" viewBox="0 0 24 24" aria-hidden="true"><rect x="3" y="6" width="18" height="12" rx="1.5" fill="none" stroke="#22a3e0" stroke-width="2"/><path d="M3.5 7l8.5 6 8.5-6" fill="none" stroke="#22a3e0" stroke-width="2"/></svg>
      </li>
      <li class="contact-item">www.rwtfittings-demo.com
        <svg class="contact-icon" viewBox="0 0 24 24" aria-hidden="true"><circle cx="12" cy="12" r="9" fill="none" stroke="#22a3e0" stroke-width="2"/><ellipse cx="12" cy="12" rx="4" ry="9" fill="none" stroke="#22a3e0" stroke-width="1.6"/><path d="M3 12h18M5 7.5h14M5 16.5h14" stroke="#22a3e0" stroke-width="1.6"/></svg>
      </li>
    </ul>
  </section>
</main>
</body>
</html>
```